Security and Technology Website - Bold and Confident, Something Unexpected

Maple Wren Systems is launching its first website and we need a great design to bring our brand to life and generate DTC and B2B leads.

We have a good logo, but I am struggling with the creative vision to bring it all together. While our industry is Alarm Systems and Technology, we want to create a site that is more friendly and less 'typical' than your standard IT sites.

It Must:
1. Appeal to both men and women. The logo is a bit masculine, so the colors and icons must soften this.
2. Feel modern - we need to convey that we we use the latest technology.
3. Feel a bit high-end. We are not a budget solution.
4. Have a distinct iconography and photo treatment.
5. Feel layered - not just a series of stacked horizontal modules.

It Should Not:
1. Feel like your typical IT website.

Here are resources to get you started!
• Staging Site:
https://maple-wren-systems.shopfrontdemo.example/
Password: Piper

•Brand Guide: https://www.layoutboard.example/design/QKRmWpLcT4V/hNbq8Yf2-ZsKeRtDw7xp-QE/edit?utm_content=QKRmWpLcT4V&utm_campaign=designshare&utm_medium=link2&utm_source=sharebutton

• Logo and Fonts and Photos: :https://files.cloudlocker.example/folders/7HtPqWmZc3Kd9RbLx2VnYs8FgJe4UoAiT?usp=sharing

• Design Inspiration (don't feel limited by this): https://www.layoutboard.example/design/QKTnHsVbWe8/p7MfRz31xYqLcKdTu9GNBw/edit?utm_content=QKTnHsVbWe8&utm_campaign=designshare&utm_medium=link2&utm_source=sharebutton

______________

The winner will be asked to provide design files and finished PNGs of the overall design file, backgrounds, photo treatments/frames, and icons.

The winner will likely be engaged for a phase 2 to build out a product page.

Industry/Entity Type

Alarm Systems, Home Theatres, and Commercial IT Networking

Number of Pages Required

1 page

Font styles to use
Sans Serif

Colors
0054AA
0677BA
7BADD7
CADEEF
E8F1F8
0094D4
00A9DD
6FCCEA
C7EBF8
E9F6FB
EB3D1F
EC4F4E
F09395
F8D3D4
FCEDEE

Requirements
Must have
• 1. Appeal to both men and women. The logo is a bit masculine, so the colors and icons must soften this. 2. Feel modern - we need to convey that we we use the latest technology. 3. Feel a bit high-end. We are not a budget solution. 4. Have a distinct iconography and photo treatment. 5. Feel layered - not just a series of stacked horizontal modules.
Should not have
• 1. Should not feel like just another IT website.

```html
<!DOCTYPE html>
<html lang="en">
<head>
<meta charset="utf-8">
<title>Maple Wren Systems — Homes + Businesses</title>
<link href="https://fonts.googleapis.com/css2?family=Montserrat:ital,wght@0,400;0,500;0,600;0,700;1,400&family=Russo+One&display=swap" rel="stylesheet">
<style>
:root{
  --blue:#1f63be;
  --blue-bright:#1c7be2;
  --blue-dark:#0054aa;
  --red:#e8201f;
  --ink:#1c1c1c;
  --text:#444;
  --muted:#7a7a7a;
  --grey:#f1f1f1;
  --footer:#242424;
  --white:#fff;
}
*{box-sizing:border-box;margin:0;padding:0}
html,body{width:1200px;height:4175px;overflow:hidden}
body{position:relative;font-family:"Montserrat",sans-serif;color:var(--ink);background:var(--white)}
.abs{position:absolute}
.display{font-family:"Russo One",sans-serif;text-transform:uppercase;letter-spacing:.5px}
.btn{position:absolute;display:flex;align-items:center;justify-content:center;gap:12px;background:var(--red);color:#fff;font-weight:700;font-size:15px;letter-spacing:.4px;text-transform:uppercase}
.btn svg{width:17px;height:17px}
.btn.outline{background:transparent;border:2px solid #fff}

/* top bar + nav */
.topbar{top:0;left:0;width:1200px;height:33px;background:var(--blue)}
.topbar span{position:absolute;top:9px;color:#fff;font-size:13px}
.social{position:absolute;top:11px;width:11px;height:11px;background:#fff;border-radius:50%}
.nav{top:33px;left:0;width:1200px;height:60px;background:#fff}
.nav a{position:absolute;top:24px;font-size:15px;font-weight:500;color:var(--ink)}
.nav a.active{color:var(--red)}
.brand-badge{position:absolute;left:518px;top:0;width:164px;height:160px;z-index:5}
.brand-badge .name{position:absolute;left:0;top:60px;width:164px;text-align:center;font-weight:700;font-size:17px;line-height:19px;color:var(--blue)}

/* hero */
.hero{top:93px;left:0;width:1200px;height:560px}
.hero-text{left:143px}
.eyebrow{top:90px;color:#fff;font-size:17px;font-weight:500}
.hero h1{top:130px;color:#fff;font-size:50px;line-height:65px;font-weight:400}
.hero p{top:267px;color:#fff;font-size:20px;font-weight:500}
.dots{left:72px;top:235px}
.dots i{display:block;width:9px;height:9px;border:2px solid #fff;border-radius:50%;margin-bottom:6px}
.dots i:first-child{background:#fff}

/* features */
.section-title{left:0;width:1200px;text-align:center;font-size:36px}
.rule{display:inline-block;width:60px;height:3px;background:var(--red);vertical-align:middle;margin:0 22px}
.lead{left:0;width:1200px;text-align:center;font-size:17px;color:var(--text)}
.feature{width:450px;height:100px}
.feature svg{position:absolute;left:0;top:0;width:97px;height:105px}
.feature h3{position:absolute;left:112px;top:10px;font-size:18px;font-weight:500;letter-spacing:.3px}
.feature p{position:absolute;left:112px;top:42px;font-size:13px;line-height:21px;color:var(--muted);width:310px}
.note{left:0;width:1200px;text-align:center;font-size:15px;line-height:29px;color:var(--text)}

/* service cards */
.greyband{top:1343px;left:0;width:1200px;height:560px;background:var(--grey)}
.svc-photo{top:1411px;width:291px;height:245px}
.svc-card{top:1609px;width:257px;height:122px;background:#fff;box-shadow:0 6px 16px rgba(0,0,0,.12);border-top:4px solid var(--blue-bright);text-align:center;padding-top:20px}
.svc-card h4{font-size:17px;font-weight:500}
.svc-card p{font-size:13px;color:var(--muted);line-height:21px;margin-top:10px;padding:0 18px}
.svc-card.hot{box-shadow:0 8px 20px rgba(232,32,31,.18)}

/* testimonial */
.testi-title{color:#fff}
.quote{left:342px;top:1978px;width:710px;color:#fff;font-style:italic;font-size:14px;line-height:25px}
.qmark{font-family:Georgia,serif;font-size:60px;color:rgba(255,255,255,.35)}
.reviewer{left:405px;top:2062px;color:#fff}
.reviewer b{font-size:15px;font-weight:600;display:block}
.reviewer small{font-size:11px}
.arrow{top:1990px;width:24px;height:36px}

/* steps */
.steps-title{left:0;width:1200px;text-align:center;font-size:33px}
.steps-title em{font-style:normal;color:var(--red)}
.numeral{position:absolute;top:2352px;font-family:"Russo One",sans-serif;font-size:120px;line-height:1;color:var(--red)}
.step{width:330px;text-align:center}
.step h4{position:absolute;top:0;left:0;width:330px;font-size:17px;font-weight:500}
.step p{position:absolute;top:33px;left:30px;width:270px;font-size:13.5px;line-height:21px;color:var(--muted)}

/* founder */
.founder h2{left:535px;top:2882px;width:560px;color:#fff;font-size:21px;font-weight:500;line-height:33px;letter-spacing:.3px}
.founder p{left:535px;top:2973px;width:525px;color:#fff;font-size:13.5px;line-height:24px}

/* quote form */
.field{position:absolute;background:#fff;border:1px solid #ddd;border-radius:3px;font-size:13px;color:#888;padding:14px 18px;display:flex;gap:8px;align-items:flex-start}
.field svg{width:12px;height:12px;margin-top:2px}

/* footer */
.footer-col h5{font-size:16px;font-weight:500;color:#fff;letter-spacing:.4px;margin-bottom:14px}
.footer-col a{display:block;color:#fff;font-size:13px;line-height:24px}
.contact-row{position:absolute;display:flex;gap:14px;color:#fff;font-size:13px;line-height:22px}
.contact-row i{flex:0 0 22px;height:22px;border-radius:50%;background:var(--blue-bright);display:flex;align-items:center;justify-content:center}
.copyright{left:0;top:4145px;width:1200px;text-align:center;color:#ddd;font-size:12.5px}
</style>
</head>
<body>

<!-- top bar -->
<div class="abs topbar">
  <span style="left:143px">&#9742; 615.555.0142</span>
  <i class="social" style="left:303px"></i>
  <i class="social" style="left:323px"></i>
  <span style="left:808px">&#9432; About</span>
  <span style="left:915px">&#128172; Project Consulting</span>
</div>
<nav class="abs nav">
  <a class="active" style="left:143px">Electronic Security</a>
  <a style="left:307px">Audio + Video</a>
  <a style="left:435px">Cabling</a>
  <a style="left:740px">Networking + Communication</a>
  <a style="left:997px">Contact</a>
</nav>
<div class="brand-badge">
  <svg width="164" height="160" viewBox="0 0 164 160"><path d="M0 0H164V110Q164 130 82 158Q0 130 0 110Z" fill="#fff" style="filter:drop-shadow(0 3px 4px rgba(0,0,0,.15))"/><circle cx="82" cy="36" r="14" fill="var(--red)"/></svg>
  <div class="name">MAPLE WREN<br>SYSTEMS</div>
</div>

<!-- hero -->
<section class="abs hero">
  <svg class="abs" width="1200" height="604" style="top:0;left:0">
    <defs><linearGradient id="heroG" x1="0" x2="1" y1="0" y2="1"><stop offset="0" stop-color="#3a4048"/><stop offset=".55" stop-color="#51606f"/><stop offset="1" stop-color="#8b97a6"/></linearGradient></defs>
    <path d="M0 0H1200V507L600 552L0 507Z" fill="url(#heroG)" role="img" aria-label="Photo of a smiling woman relaxing on a sofa with a remote and a bowl of popcorn"/>
    <path d="M349 556L600 592L851 556L851 560L600 604L349 560Z" fill="var(--red)"/>
  </svg>
  <div class="abs dots"><i></i><i></i><i></i></div>
  <div class="abs hero-text eyebrow">Homes + Businesses</div>
  <h1 class="abs hero-text display">Proudly Serving<br>Middle Tennessee</h1>
  <p class="abs hero-text">Safer. Smarter. Faster.</p>
  <a class="btn" style="left:143px;top:332px;width:177px;height:45px">Get Started <svg viewBox="0 0 16 16"><path d="M3 13L13 3M5 3H13V11" stroke="#fff" stroke-width="2" fill="none"/></svg></a>
</section>

<!-- connect + protect -->
<h2 class="abs section-title display" style="top:762px"><span class="rule"></span>Connect + Protect Your World<span class="rule"></span></h2>
<p class="abs lead" style="top:827px">Protect your people, assets, and information from whatever comes.</p>

<svg width="0" height="0" style="position:absolute">
  <defs>
    <symbol id="hex" viewBox="0 0 97 105"><path d="M48.5 2L94 28V77L48.5 103L3 77V28Z" fill="#fff" stroke="var(--red)" stroke-width="3"/><path d="M48.5 10L87 32V73L48.5 95L10 73V32Z" fill="var(--blue-bright)"/></symbol>
  </defs>
</svg>

<div class="abs feature" style="left:146px;top:882px">
  <svg viewBox="0 0 97 105"><use href="#hex"/><path d="M34 46Q48.5 34 63 46M39 53Q48.5 45 58 53" stroke="#fff" stroke-width="3" fill="none"/><rect x="36" y="60" width="25" height="6" rx="3" fill="#fff"/></svg>
  <h3>ENTRY &amp; MOTION SENSORS</h3>
  <p>Pair text with an icon to focus on your chosen product, collection, or blog post.</p>
</div>
<div class="abs feature" style="left:646px;top:882px">
  <svg viewBox="0 0 97 105"><use href="#hex"/><rect x="37" y="32" width="23" height="40" rx="3" fill="none" stroke="#fff" stroke-width="3"/><circle cx="48.5" cy="44" r="4" fill="#fff"/><path d="M43 64Q43 55 48.5 55Q54 55 54 64Z" fill="#fff"/></svg>
  <h3>VIDEO DOORBELLS</h3>
  <p>Pair text with an icon to focus on your chosen product, collection, or blog post.</p>
</div>
<div class="abs feature" style="left:146px;top:1006px">
  <svg viewBox="0 0 97 105"><use href="#hex"/><rect x="30" y="42" width="32" height="16" rx="3" transform="rotate(20 46 50)" fill="#fff"/><path d="M58 58V72M54 72H66" stroke="#fff" stroke-width="3"/></svg>
  <h3>SECURITY CAMERAS</h3>
  <p>Pair text with an icon to focus on your chosen product, collection, or blog post.</p>
</div>
<div class="abs feature" style="left:646px;top:1006px">
  <svg viewBox="0 0 97 105"><use href="#hex"/><path d="M48.5 68L34 54Q28 46 35 40Q42 35 48.5 43Q55 35 62 40Q69 46 63 54Z" fill="#fff"/></svg>
  <h3>PET-FRIENDLY</h3>
  <p>Pair text with an icon to focus on your chosen product, collection, or blog post.</p>
</div>

<p class="abs note" style="top:1140px">Our team is always on guard. With always-on protection, we'll notify you of any suspicious activity.<br>In emergencies, we'll monitor your local police, fire, or EMS.</p>
<a class="btn" style="left:535px;top:1228px;width:130px;height:44px">Button <svg viewBox="0 0 16 16"><path d="M3 13L13 3M5 3H13V11" stroke="#fff" stroke-width="2" fill="none"/></svg></a>

<!-- services -->
<div class="abs greyband"></div>
<div class="abs svc-photo" style="left:144px;background:linear-gradient(135deg,#8a6a55,#d9d2c9)" role="img" aria-label="Photo of a woman using a wall-mounted security keypad"></div>
<div class="abs svc-photo" style="left:454px;background:linear-gradient(135deg,#4b4036,#b49a72)" role="img" aria-label="Photo of a home theatre room with a large screen"></div>
<div class="abs svc-photo" style="left:764px;background:linear-gradient(135deg,#3a4350,#c9ccd2)" role="img" aria-label="Photo of a business video conference meeting"></div>
<div class="abs svc-card" style="left:160px"><h4>Affordable Security</h4><p>For Homes · For Businesses</p></div>
<div class="abs svc-card hot" style="left:471px"><h4>Enviable Entertainment</h4><p>Home Theatres · Smart Homes · Whole Home A/V</p></div>
<div class="abs svc-card" style="left:781px"><h4>Connected Businesses</h4><p>Conference Systems · Phones · Networking · WiFi</p></div>

<!-- testimonials -->
<svg class="abs" width="1200" height="370" style="top:1795px;left:0">
  <path d="M0 106L600 11L1200 106V370H0Z" fill="var(--blue)"/>
  <path d="M349 55L600 0L851 55L851 58L600 14L349 58Z" fill="var(--red)"/>
</svg>
<h2 class="abs section-title display testi-title" style="top:1912px;font-size:32px"><span class="rule"></span>Client Testimonials<span class="rule"></span></h2>
<svg class="abs arrow" style="left:71px" viewBox="0 0 24 36"><path d="M18 4L6 18L18 32" stroke="#fff" stroke-width="4" fill="none"/></svg>
<svg class="abs arrow" style="left:1105px" viewBox="0 0 24 36"><path d="M6 4L18 18L6 32" stroke="#fff" stroke-width="4" fill="none"/></svg>
<svg class="abs" width="122" height="125" style="left:182px;top:1951px" role="img" aria-label="Headshot of the reviewer">
  <defs><linearGradient id="revG" x1="0" y1="0" x2="0" y2="1"><stop offset="0" stop-color="#e9e6e2"/><stop offset="1" stop-color="#4d5563"/></linearGradient></defs>
  <path d="M61 0L122 62L61 125L0 62Z" fill="url(#revG)"/>
</svg>
<div class="abs qmark" style="left:300px;top:1942px">&ldquo;</div>
<div class="abs qmark" style="left:920px;top:2025px">&rdquo;</div>
<p class="abs quote">Lorem ipsum dolor sit amet, consectetur adipiscing elit, sed do eiusmod tempor incididunt ut labore et dolore magna aliqua. Ut enim ad minim veniam, quis nostrud exercitation ullamco laboris nisi ut aliquip ex ea commodo consequat. Duis aute irure dolor in reprehenderit voluptate</p>
<div class="abs" style="left:342px;top:2061px;width:40px;height:40px;border-radius:50%;background:#fff"></div>
<div class="abs reviewer"><b>Marla Quinn</b><small>CEO</small></div>

<!-- steps -->
<h2 class="abs steps-title display" style="top:2255px">A Safer Home or Business is as Easy as <em>1–2–3</em></h2>

<svg class="abs" width="1200" height="160" style="top:2334px;left:0">
  <g fill="#fff" stroke="var(--red)" stroke-width="2.5">
    <circle cx="318" cy="76" r="72"/><circle cx="620" cy="76" r="72"/><circle cx="938" cy="76" r="72"/>
  </g>
  <!-- step 1: quote blocks -->
  <g fill="var(--blue-bright)">
    <rect x="292" y="80" width="20" height="20"/><rect x="314" y="58" width="20" height="20"/><rect x="334" y="40" width="18" height="16"/><rect x="282" y="102" width="14" height="14"/><rect x="316" y="82" width="12" height="12"/>
  </g>
  <!-- step 2: gear with tick -->
  <g fill="var(--blue-bright)">
    <circle cx="626" cy="72" r="26"/>
    <rect x="621" y="40" width="10" height="10"/><rect x="621" y="94" width="10" height="10"/><rect x="594" y="67" width="10" height="10"/><rect x="648" y="67" width="10" height="10"/>
  </g>
  <circle cx="626" cy="72" r="10" fill="#fff"/>
  <circle cx="648" cy="94" r="13" fill="var(--blue-dark)" stroke="#fff" stroke-width="2"/>
  <path d="M642 94L647 99L655 89" stroke="#fff" stroke-width="3" fill="none"/>
  <!-- step 3: shield over hand -->
  <g fill="var(--blue-bright)">
    <path d="M948 36L970 44V60Q970 78 948 88Q926 78 926 60V44Z"/>
    <path d="M910 100H940L958 92Q966 92 962 100L944 112H910Z"/>
  </g>
  <path d="M939 60L946 67L958 53" stroke="#fff" stroke-width="3" fill="none"/>
</svg>
<span class="numeral" style="left:196px">1</span>
<span class="numeral" style="left:504px">2</span>
<span class="numeral" style="left:818px">3</span>

<div class="abs step" style="left:121px;top:2507px"><h4>Build an Instant Quote</h4><p>Our live-estimate builder will guide you through a few questions to help us understand your needs.</p></div>
<div class="abs step" style="left:433px;top:2507px"><h4>Schedule Installation</h4><p>Our trained techs are efficient and friendly. Southern-born and raised we will respect your home and your schedule.</p></div>
<div class="abs step" style="left:749px;top:2507px"><h4>Stay Secure 24/7</h4><p>Monitor your home through the app, receive instant alerts, and rely on professional monitoring services for emergencies.</p></div>
<a class="btn" style="left:517px;top:2673px;width:164px;height:44px">Get Started <svg viewBox="0 0 16 16"><path d="M3 13L13 3M5 3H13V11" stroke="#fff" stroke-width="2" fill="none"/></svg></a>

<!-- founder -->
<svg class="abs" width="1200" height="500" style="top:2790px;left:0">
  <path d="M0 0H1200V397L600 460L0 397Z" fill="var(--blue-bright)"/>
  <path d="M349 450L600 490L851 450L851 454L600 500L349 454Z" fill="var(--red)"/>
  <defs><linearGradient id="fdG" x1="0" y1="0" x2="0" y2="1"><stop offset="0" stop-color="#dbe8f4"/><stop offset="1" stop-color="#2a3550"/></linearGradient></defs>
  <path d="M302 32L466 126V314L302 409L138 314V126Z" fill="#fff" stroke="var(--red)" stroke-width="3"/>
  <path d="M302 44L455 132V308L302 397L149 308V132Z" fill="url(#fdG)" role="img" aria-label="Portrait of the company founder in a suit and bow tie"/>
</svg>
<div class="founder">
  <h2 class="abs">I Founded Maple Wren Systems To Bring Together Technology &amp; Honest, Reliable Service.</h2>
  <p class="abs">I'm proud to call Tennessee home and even prouder to help keep its homes and businesses secure Whether it's protecting or elevating your space, my goal is to make technology work for you. Think of us as your friendly, neighborhood tech expert—here to safeguard what matters most.</p>
</div>
<a class="btn" style="left:535px;top:3090px;width:284px;height:44px">Tell Us How We Can Help <svg viewBox="0 0 16 16"><path d="M3 13L13 3M5 3H13V11" stroke="#fff" stroke-width="2" fill="none"/></svg></a>
<a class="btn outline" style="left:832px;top:3090px;width:154px;height:44px">About Us <svg viewBox="0 0 16 16"><path d="M3 13L13 3M5 3H13V11" stroke="#fff" stroke-width="2" fill="none"/></svg></a>

<!-- request a quote -->
<h2 class="abs section-title display" style="top:3352px;font-size:33px">Request a Quote</h2>
<div class="abs" style="left:558px;top:3411px;width:84px;height:4px;background:var(--red)"></div>
<div class="field" style="left:180px;top:3455px;width:409px;height:46px"><svg viewBox="0 0 12 12"><rect x="2" y="5" width="8" height="6" fill="none" stroke="#999"/><path d="M4 5V3Q6 0 8 3V5" fill="none" stroke="#999"/></svg>First Name</div>
<div class="field" style="left:610px;top:3455px;width:409px;height:46px"><svg viewBox="0 0 12 12"><rect x="2" y="5" width="8" height="6" fill="none" stroke="#999"/><path d="M4 5V3Q6 0 8 3V5" fill="none" stroke="#999"/></svg>Last Name</div>
<div class="field" style="left:180px;top:3525px;width:409px;height:47px"><svg viewBox="0 0 12 12"><rect x="1" y="2" width="10" height="8" fill="#999"/></svg>Email Address</div>
<div class="field" style="left:610px;top:3525px;width:409px;height:47px"><svg viewBox="0 0 12 12"><path d="M2 1L5 4L4 6Q6 8 7 8L8 7L11 10L9 11Q1 8 1 3Z" fill="#999"/></svg>Phone Number</div>
<div class="field" style="left:180px;top:3596px;width:839px;height:102px"><svg viewBox="0 0 12 12"><ellipse cx="6" cy="5" rx="5" ry="4" fill="#999"/></svg>Message</div>
<a class="btn" style="left:517px;top:3734px;width:164px;height:42px">Submit Now <svg viewBox="0 0 16 16"><path d="M3 13L13 3M5 3H13V11" stroke="#fff" stroke-width="2" fill="none"/></svg></a>

<!-- footer -->
<svg class="abs" width="1200" height="340" style="top:3835px;left:0">
  <path d="M0 90L600 14L1200 90V340H0Z" fill="var(--footer)"/>
  <path d="M349 52L600 0L851 52L851 56L600 12L349 56Z" fill="var(--red)"/>
</svg>
<div class="abs" style="left:143px;top:4008px;width:141px;text-align:center;color:#fff;font-weight:700;font-size:19px;line-height:22px">MAPLE WREN<br>SYSTEMS</div>
<div class="abs" style="left:203px;top:3978px;width:20px;height:20px;border-radius:50%;background:#fff"></div>
<div class="abs footer-col" style="left:363px;top:3950px"><h5>RESIDENTIAL</h5><a>Home Security</a><a>Smart Homes</a><a>Home Theatres + A/V</a><a>WiFi</a><a>Cabling</a></div>
<div class="abs footer-col" style="left:598px;top:3950px"><h5>COMMERCIAL</h5><a style="line-height:21px">Audio Video</a><a style="line-height:21px">Cabling</a><a style="line-height:21px">Communication</a><a style="line-height:21px">Electronic Security</a><a style="line-height:21px">Project Consulting</a></div>
<div class="abs footer-col" style="left:832px;top:3950px"><h5>CONTACT US</h5></div>
<div class="contact-row" style="left:832px;top:3988px"><i><svg width="11" height="11" viewBox="0 0 12 12"><path d="M2 1L5 4L4 6Q6 8 7 8L8 7L11 10L9 11Q1 8 1 3Z" fill="#fff"/></svg></i>615.555.0142</div>
<div class="contact-row" style="left:832px;top:4026px"><i><svg width="10" height="12" viewBox="0 0 10 12"><path d="M5 12Q0 6 0 5A5 5 0 0 1 10 5Q10 6 5 12Z" fill="#fff"/><circle cx="5" cy="5" r="2" fill="var(--blue-bright)"/></svg></i><span>482 Harbor Ridge Dr. Suite 2-110<br>Brookhaven, TN 37099</span></div>
<div class="abs" style="left:143px;top:4127px;width:914px;height:1px;background:#444"></div>
<p class="abs copyright">Copyright© 2024 Maple Wren Systems &nbsp;|&nbsp; All Rights Reserved</p>

</body>
</html>
```